Load Up Your Cart

Require two banners with a size of 980 x 450 pixels
Similar natural looking banner as per attachment. The background is supposed to be a cardboard carton
price "$9.95"
Wording and layout the same as attached file

```html
<!DOCTYPE html>
<html lang="en">
<head>
<meta charset="utf-8">
<title>Load Up Your Cart – Flat Rate Shipping</title>
<link rel="stylesheet" href="https://fonts.googleapis.com/css2?family=Questrial&family=Oswald:wght@700&family=Stardos+Stencil:wght@700&display=swap">
<style>
  :root {
    --carton-light: #a96e35;
    --carton-mid: #94592a;
    --carton-dark: #7a4519;
    --carton-fibre: rgba(60, 30, 8, 0.06);
    --carton-flute: rgba(255, 220, 160, 0.035);
    --ring-yellow: #ffcc00;
    --soft-yellow: #f8d867;
    --price-yellow: #ffcf00;
    --label-yellow: #f2c73c;
  }
  html, body {
    margin: 0;
    padding: 0;
    width: 1200px;
    height: 551px;
    overflow: hidden;
    background: var(--carton-dark);
  }
  .banner {
    position: relative;
    width: 1200px;
    height: 551px;
    background:
      repeating-linear-gradient(90deg, var(--carton-flute) 0 3px, transparent 3px 9px),
      repeating-linear-gradient(87deg, var(--carton-fibre) 0 1px, transparent 1px 23px),
      radial-gradient(ellipse 75% 95% at 56% 28%, var(--carton-light) 0%, var(--carton-mid) 55%, var(--carton-dark) 100%);
  }
  .banner svg {
    display: block;
    width: 1200px;
    height: 551px;
  }
  .carton-grain {
    opacity: 0.16;
    mix-blend-mode: multiply;
  }
  .badge-ring {
    fill: none;
    stroke: var(--ring-yellow);
    stroke-width: 12;
  }
  .badge-word {
    font-family: "Questrial", sans-serif;
    fill: var(--soft-yellow);
  }
  .price {
    font-family: "Oswald", sans-serif;
    font-weight: 700;
    fill: var(--price-yellow);
  }
  .offer-title,
  .offer-terms {
    font-family: "Stardos Stencil", serif;
    font-weight: 700;
  }
  .offer-title { fill: var(--label-yellow); }
  .offer-terms { fill: var(--soft-yellow); }
</style>
</head>
<body>
<main class="banner">
  <svg viewBox="0 0 1200 551" xmlns="http://www.w3.org/2000/svg">
    <defs>
      <filter id="carton-grain-filter" x="0" y="0" width="100%" height="100%">
        <feTurbulence type="fractalNoise" baseFrequency="0.9 0.035" numOctaves="3" seed="7"/>
        <feColorMatrix type="matrix" values="0 0 0 0 0.35  0 0 0 0 0.18  0 0 0 0 0.05  0 0 0 1.2 -0.2"/>
      </filter>
    </defs>
    <rect class="carton-grain" x="0" y="0" width="1200" height="551" filter="url(#carton-grain-filter)"/>

    <g class="badge">
      <circle class="badge-ring" cx="276" cy="276" r="238"/>
      <g transform="rotate(-13 276 276)">
        <text class="badge-word badge-load" x="122" y="231" font-size="128" textLength="335" lengthAdjust="spacingAndGlyphs">LOAD</text>
        <text class="badge-word badge-up" x="110" y="375" font-size="130" textLength="138" lengthAdjust="spacingAndGlyphs">UP</text>
        <text class="badge-word badge-your" x="281" y="334" font-size="56" textLength="145" lengthAdjust="spacingAndGlyphs">YOUR</text>
        <text class="badge-word badge-cart" x="283" y="399" font-size="56" textLength="137" lengthAdjust="spacingAndGlyphs">CART</text>
      </g>
    </g>

    <text class="price" x="857" y="246" text-anchor="middle" font-size="178" textLength="306" lengthAdjust="spacingAndGlyphs">$9.95</text>
    <text class="offer-title" x="839" y="393" text-anchor="middle" font-size="78" textLength="600" lengthAdjust="spacingAndGlyphs">FLAT RATE SHIPPING</text>
    <text class="offer-terms" x="830" y="485" text-anchor="middle" font-size="50" textLength="722" lengthAdjust="spacingAndGlyphs">NO MINIMUMS. NO CODES. NO GIMMICKS.</text>
  </svg>
</main>
</body>
</html>
```